Agriculture farming Hemp and CBD

The logo is in works with your company now, should be ready in a few days. We have our Domain (kestrelbrookhollow.com) We would like to see incorporated seed to growth, but not necessary. we would like to nature colors and some black and green. we have our farm and will be growing and selling HEMP and CBD we are based in the state of Virginia. Would like to incorporate the words pause, play, rewind if possible but not necessary.

Target Market(s)

20 years old to elderly

Coding

Coded - Design and coding required

Number of Pages Required

3 page

Font styles to use
Serif

Requirements
Must have
• I'm not sure on the must haves, we are open to any ideas, we would definitely like to see Hemp and CBD included, may the life cycle of seed to plant. We must have a pop up asking if you are 20 years old before they can enter our site and to view or purchase our product. I want the design to be totally different than what i uploaded.
Nice to have
• Would like to see natural colors as well as black and green
Should not have
• I want

```html
<!DOCTYPE html>
<html lang="en">
<head>
<meta charset="utf-8">
<title>Kestrel Brook Hollow – Products</title>
<link rel="stylesheet" href="https://fonts.googleapis.com/css2?family=Open+Sans:wght@400;600;700;800&display=swap">
<style>
:root{
  --black:#000;
  --green:#1ee81e;
  --green-dark:#13c213;
  --white:#fff;
  --ink:#222;
  --muted:#888;
  --line:#e4e4e4;
  --card-bg:#f6f6f6;
}
*{box-sizing:border-box;margin:0;padding:0}
html,body{width:1200px;height:2963px;overflow:hidden}
body{position:relative;font-family:"Open Sans",sans-serif;color:var(--ink);background:var(--white)}

.site-header{position:absolute;left:0;top:0;width:1200px;height:120px;background:var(--black);color:var(--white)}
.brand{position:absolute;left:42px;top:62px;font-size:21px;font-weight:700;color:var(--white);white-space:nowrap}
.main-nav{position:absolute;left:371px;top:68px;font-size:16px;font-weight:700}
.main-nav span{position:absolute;white-space:nowrap}
.caret{display:inline-block;width:7px;height:7px;border-right:1.5px solid var(--green);border-bottom:1.5px solid var(--green);transform:rotate(45deg);margin-left:6px;position:relative;top:-3px}
.header-icons svg{position:absolute}

.hero{position:absolute;left:0;top:120px;width:1200px;height:604px;background:radial-gradient(ellipse at 70% 40%,#6f9a55 0%,#3f6b32 45%,#1f3d1b 100%)}
.hero-bar{position:absolute;left:133px;top:360px;width:3px;height:157px;background:var(--green)}
.hero-kicker{position:absolute;left:166px;top:352px;font-size:42px;font-weight:800;color:var(--green);line-height:1}
.hero-title{position:absolute;left:166px;top:405px;font-size:53px;font-weight:800;color:var(--white);line-height:62px}

.crumbs{position:absolute;left:87px;top:755px;font-size:15px;color:#333}
.crumbs i{color:var(--green);font-style:normal;margin:0 10px}
.tab{position:absolute;top:750px;font-size:20px;font-weight:700;color:#333}
.tab-active{color:var(--green)}
.tab-sep{position:absolute;top:750px;width:1px;height:26px;background:#999}
.sort{position:absolute;left:995px;top:753px;font-size:16px;color:var(--muted)}
.rule{position:absolute;left:40px;top:791px;width:1130px;height:1px;background:linear-gradient(90deg,transparent,var(--green-dark) 20%,var(--green-dark) 80%,transparent)}

.filters-title{position:absolute;left:88px;top:822px;font-size:21px;font-weight:700;color:var(--green)}
.f-rule{position:absolute;left:86px;width:170px;height:1px;background:var(--line)}
.f-head{position:absolute;left:86px;font-size:21px;font-weight:700;color:#111}
.f-chev{position:absolute;left:238px;width:10px;height:10px;border-right:2px solid var(--green);border-bottom:2px solid var(--green);transform:rotate(45deg)}
.f-opt{position:absolute;left:90px;font-size:19px;color:#222}
.f-opt::before{content:"";display:inline-block;width:9px;height:9px;border:1.5px solid #333;border-radius:50%;margin-right:17px;vertical-align:middle}

.card{position:absolute;width:256px;height:333px;border:2px solid var(--green);border-radius:4px;overflow:hidden;background:var(--black)}
.card-media{height:192px;background:radial-gradient(circle at 50% 52%,#7b8a5c 0%,#5f6b45 28%,var(--card-bg) 50%)}
.card-body{padding:16px 0 0 18px;color:var(--white)}
.card-name{font-size:16px;font-weight:700}
.card-price{font-size:21px;font-weight:700;margin-top:4px}
.card-price s{color:var(--white);margin-right:6px}
.card-price b{color:var(--green)}
.card-actions{margin-top:15px;display:flex;gap:12px}
.btn{width:63px;height:26px;border-radius:13px;font-size:15px;text-align:center;line-height:24px}
.btn-view{border:1.5px solid var(--green);color:var(--green)}
.btn-buy{background:var(--green);color:#0a3b0a}

.view-more{position:absolute;left:684px;top:2384px;font-size:16px;font-weight:700;font-style:italic;color:var(--green-dark);text-decoration:underline}

.footer{position:absolute;left:0;top:2462px;width:1200px;height:435px;background:linear-gradient(180deg,#fbfbfb,#f3f5f1);border-top:2px solid #eee}
.socials{position:absolute;left:551px;top:2538px;display:flex;gap:11px}
.socials span{width:16px;height:16px;border-radius:50%;border:2px solid #111}
.sub-label{position:absolute;left:0;width:1200px;top:2577px;text-align:center;font-size:16px;color:#222}
.sub-input{position:absolute;left:403px;top:2607px;width:278px;height:41px;border:1.5px solid #555;border-radius:21px;padding-left:20px;line-height:38px;font-size:16px;color:#888}
.sub-btn{position:absolute;left:686px;top:2607px;width:109px;height:41px;border-radius:21px;background:var(--black);color:var(--green);font-size:15px;font-weight:800;text-align:center;line-height:41px}
.f-col{position:absolute;top:2688px;font-size:16px;line-height:28px;color:#222}
.f-contact{left:783px;top:2692px;line-height:21px}
.bottom-bar{position:absolute;left:0;top:2897px;width:1200px;height:66px;background:var(--black);color:var(--white);font-size:16px}
.bottom-bar p{position:absolute;left:802px;top:22px}
.bottom-bar em{font-style:normal;color:var(--green)}
</style>
</head>
<body>

<header class="site-header">
  <div class="brand">kestrelbrookhollow.com</div>
  <nav class="main-nav">
    <span style="left:0">Home</span>
    <span style="left:109px">About<i class="caret"></i></span>
    <span style="left:217px">Products<i class="caret"></i></span>
    <span style="left:349px">Blogs</span>
    <span style="left:454px">Shop<i class="caret"></i></span>
    <span style="left:557px">Contact</span>
  </nav>
  <div class="header-icons">
    <svg style="left:1051px;top:66px" width="22" height="22" viewBox="0 0 22 22" fill="none" stroke="#fff" stroke-width="2"><circle cx="9" cy="9" r="7"/><line x1="14" y1="14" x2="20" y2="20"/></svg>
    <svg style="left:1093px;top:64px" width="20" height="24" viewBox="0 0 20 24" fill="none" stroke="#fff" stroke-width="2"><path d="M2 8h16l-1 14H3z"/><path d="M6 8V5a4 4 0 0 1 8 0v3"/></svg>
    <svg style="left:1102px;top:52px" width="15" height="15"><circle cx="7.5" cy="7.5" r="7.5" fill="#1ee81e"/><text x="7.5" y="11" font-size="10" text-anchor="middle" fill="#000" font-family="Open Sans,sans-serif">3</text></svg>
    <svg style="left:1134px;top:68px" width="22" height="18" stroke="#1ee81e" stroke-width="2"><line x1="2" y1="2" x2="20" y2="2"/><line x1="2" y1="9" x2="20" y2="9"/><line x1="2" y1="16" x2="20" y2="16"/></svg>
  </div>
</header>

<section class="hero" role="img" aria-label="Hand holding a hemp leaf in front of a blurred green hemp field"></section>
<div class="hero-bar"></div>
<div class="hero-kicker">VIRGINIA GROWN</div>
<div class="hero-title">EXPERTISE IN HEMP<br>CULTIVATION</div>

<div class="crumbs">Home<i>›</i>Products</div>
<div class="tab tab-active" style="left:301px">ALL</div>
<div class="tab-sep" style="left:375px"></div>
<div class="tab" style="left:390px">FLOWERS</div>
<div class="tab-sep" style="left:517px"></div>
<div class="tab" style="left:538px">EDIBLES</div>
<div class="tab-sep" style="left:658px"></div>
<div class="tab" style="left:680px">INFUSIONS</div>
<div class="sort">Sort By <i class="caret" style="border-width:2px"></i></div>
<div class="rule"></div>

<aside>
  <div class="filters-title">Filters</div>
  <div class="f-rule" style="top:864px"></div>
  <div class="f-head" style="top:870px">Categories</div><div class="f-chev" style="top:877px"></div>
  <div class="f-opt" style="top:913px">All</div>
  <div class="f-opt" style="top:944px">Flowers</div>
  <div class="f-opt" style="top:974px">Edibles</div>
  <div class="f-opt" style="top:1005px">Infusions</div>
  <div class="f-opt" style="top:1035px">Oil</div>
  <div class="f-head" style="top:1073px">Offers</div><div class="f-chev" style="top:1080px"></div>
  <div class="f-rule" style="top:1105px"></div>
  <div class="f-head" style="top:1112px">Price</div><div class="f-chev" style="top:1119px"></div>
  <div class="f-rule" style="top:1149px"></div>
  <div class="f-head" style="top:1152px">More Filters</div><div class="f-chev" style="top:1159px"></div>
  <div class="f-rule" style="top:1197px"></div>
</aside>

<main>
  <article class="card" style="left:301px;top:857px"><div class="card-media" role="img" aria-label="Hemp flower bud"></div><div class="card-body"><div class="card-name">AAA Rockstar</div><div class="card-price"><s>$11.20</s><b>$7.99</b></div><div class="card-actions"><div class="btn btn-view">View</div><div class="btn btn-buy">Buy</div></div></div></article>
  <article class="card" style="left:594px;top:857px"><div class="card-media" role="img" aria-label="Hemp flower bud"></div><div class="card-body"><div class="card-name">Manjura weed</div><div class="card-price"><s>$11.20</s><b>$7.99</b></div><div class="card-actions"><div class="btn btn-view">View</div><div class="btn btn-buy">Buy</div></div></div></article>
  <article class="card" style="left:879px;top:857px"><div class="card-media" role="img" aria-label="Hemp flower bud"></div><div class="card-body"><div class="card-name">HEMP Flower</div><div class="card-price"><s>$11.20</s><b>$7.99</b></div><div class="card-actions"><div class="btn btn-view">View</div><div class="btn btn-buy">Buy</div></div></div></article>

  <article class="card" style="left:301px;top:1228px"><div class="card-media" role="img" aria-label="Hemp flower bud"></div><div class="card-body"><div class="card-name">AAA Rockstar</div><div class="card-price"><s>$11.20</s><b>$7.99</b></div><div class="card-actions"><div class="btn btn-view">View</div><div class="btn btn-buy">Buy</div></div></div></article>
  <article class="card" style="left:594px;top:1228px"><div class="card-media" role="img" aria-label="Pre-rolled hemp cones"></div><div class="card-body"><div class="card-name">Manjura weed</div><div class="card-price"><s>$11.20</s><b>$7.99</b></div><div class="card-actions"><div class="btn btn-view">View</div><div class="btn btn-buy">Buy</div></div></div></article>
  <article class="card" style="left:879px;top:1228px"><div class="card-media" role="img" aria-label="Hemp flower bud"></div><div class="card-body"><div class="card-name">HEMP Flower</div><div class="card-price"><s>$11.20</s><b>$7.99</b></div><div class="card-actions"><div class="btn btn-view">View</div><div class="btn btn-buy">Buy</div></div></div></article>

  <article class="card" style="left:301px;top:1598px"><div class="card-media" role="img" aria-label="Hemp flower bud"></div><div class="card-body"><div class="card-name">AAA Rockstar</div><div class="card-price"><s>$11.20</s><b>$7.99</b></div><div class="card-actions"><div class="btn btn-view">View</div><div class="btn btn-buy">Buy</div></div></div></article>
  <article class="card" style="left:594px;top:1598px"><div class="card-media" role="img" aria-label="Hemp flower bud"></div><div class="card-body"><div class="card-name">Manjura weed</div><div class="card-price"><s>$11.20</s><b>$7.99</b></div><div class="card-actions"><div class="btn btn-view">View</div><div class="btn btn-buy">Buy</div></div></div></article>
  <article class="card" style="left:879px;top:1598px"><div class="card-media" role="img" aria-label="Hemp flower bud"></div><div class="card-body"><div class="card-name">HEMP Flower</div><div class="card-price"><s>$11.20</s><b>$7.99</b></div><div class="card-actions"><div class="btn btn-view">View</div><div class="btn btn-buy">Buy</div></div></div></article>

  <article class="card" style="left:301px;top:1978px"><div class="card-media" role="img" aria-label="Hemp flower bud"></div><div class="card-body"><div class="card-name">AAA Rockstar</div><div class="card-price"><s>$11.20</s><b>$7.99</b></div><div class="card-actions"><div class="btn btn-view">View</div><div class="btn btn-buy">Buy</div></div></div></article>
  <article class="card" style="left:594px;top:1978px"><div class="card-media" role="img" aria-label="Hemp flower bud"></div><div class="card-body"><div class="card-name">Manjura weed</div><div class="card-price"><s>$11.20</s><b>$7.99</b></div><div class="card-actions"><div class="btn btn-view">View</div><div class="btn btn-buy">Buy</div></div></div></article>
  <article class="card" style="left:879px;top:1978px"><div class="card-media" role="img" aria-label="Hemp flower bud"></div><div class="card-body"><div class="card-name">HEMP Flower</div><div class="card-price"><s>$11.20</s><b>$7.99</b></div><div class="card-actions"><div class="btn btn-view">View</div><div class="btn btn-buy">Buy</div></div></div></article>

  <div class="view-more">View More</div>
</main>

<footer>
  <div class="footer" role="img" aria-label="Faint hemp leaves in the background"></div>
  <div class="socials"><span></span><span></span><span></span><span></span></div>
  <div class="sub-label">SUBSCRIBE TO OUR NEWSLETTER</div>
  <div class="sub-input">Enter e-mail id</div>
  <div class="sub-btn">SUBSCRIBE</div>
  <div class="f-col" style="left:213px">ABOUT US<br>PRODUCTS<br>BLOGS<br>SITEMAP<br>CONTACT<br>HELP CENTRE</div>
  <div class="f-col" style="left:390px">HEMP<br>CBD OIL<br>EDIBLE<br>FLOWERS</div>
  <div class="f-col" style="left:546px">TERMS &amp; CONDITION<br>PRIVACY POLICY<br>COPYRIGHTS<br>PRODUCTS<br>NEW ARRIVALS</div>
  <div class="f-col f-contact">MONDAY- FRIDAY 9.00 - 19.00<br>mhale@kestrelbrookhollow.com<br>(000) 5550 4412</div>
  <div class="bottom-bar"><p>© 2020 <em>Kestrelbrookhollow</em> . All rights reserved.</p></div>
</footer>

</body>
</html>
```